redesign of my existing custom website into Wordpress based website

I need someone to redesign my current website into something more classy, simplistic, modern and on trend. I would like it set up on Wordpress in a way thats easy for me to make my own additions to blogs/price changes and promotion banners. I will also need a page that is password protected so members can login and have access to all my training videos and resources.
website is www.tidewellmamas.com.au

Target Market(s)

new mums

Industry/Entity Type

Fitness

Coding

Coded - Design and coding required

Number of Pages Required

5+ page

Colors
33a6d7

Requirements
Must have
• chic, modern, stylish and simplistic.
• a call to action above the page fold
• mobile friendly conversion
• a pop up message as soon as someone enters my sight offering my free report
• a members page that is password protected containing 3 youtube videos and 6 pdf attachments as resources
• a home page
• a contact us page
• an about us page
• a blog page
• a store page
Nice to have
• some examples of my peers websites that I like:
• www.norapellwick.com
• https://www.9qlr.com
• https://41bytedgarth.com
Should not have
• anything gimmicky

```html
<!DOCTYPE html>
<html lang="en">
<head>
<meta charset="utf-8">
<title>Tidewell Mamas – Home Fitness</title>
<link rel="stylesheet" href="https://fonts.googleapis.com/css2?family=Lato:wght@400;700;900&family=Open+Sans:wght@400;600;700&family=Kaushan+Script&display=swap">
<style>
:root{
  --brand:#33a6d7;
  --brand-deep:#2b8fbd;
  --band:#2a86b3;
  --band-dark:#1f729c;
  --ink:#333a40;
  --muted:#6a7379;
  --olive:#c4b13a;
  --berry:#b0186f;
  --red:#e02424;
  --footer:#1c1c1c;
  --footer-low:#121212;
  --white:#ffffff;
  --shade:rgba(0,0,0,.58);
}
*{box-sizing:border-box;margin:0;padding:0}
html,body{width:1200px;height:3593px;overflow:hidden}
body{position:relative;font-family:"Open Sans",sans-serif;color:var(--ink);background:var(--white)}
.abs{position:absolute}
.heading{font-family:"Lato",sans-serif;font-weight:900;text-transform:uppercase;letter-spacing:.5px}
.copy{font-size:12.5px;line-height:18px;color:var(--muted)}
.btn{position:absolute;background:var(--brand-deep);color:var(--white);font-family:"Lato",sans-serif;font-size:15px;display:flex;align-items:center;justify-content:center;border-radius:2px}

/* header & hero */
.hero{left:0;top:0;width:1200px;height:558px;background:linear-gradient(100deg,#f4f4f6 0%,#eceaf0 45%,#d9d3dd 70%,#cfc8d4 100%)}
.hero-photo{left:560px;top:0;width:640px;height:558px;background:linear-gradient(90deg,rgba(236,232,240,0) 0%,#d6cdd6 35%,#c4b7c2 70%,#b9b2ba 100%)}
.brand{left:96px;top:12px;display:flex;align-items:center;gap:10px;font-family:"Lato",sans-serif;font-weight:700;font-size:20px;color:var(--band-dark)}
.brand-dot{width:44px;height:44px;border-radius:50%;background:var(--band-dark)}
.brand small{display:block;font-size:11px;letter-spacing:2px;color:var(--ink);font-weight:400}
.nav{left:360px;top:26px;display:flex;gap:52px;font-family:"Lato",sans-serif;font-size:15px;color:#222}
.nav .join{position:absolute;left:618px;top:-6px;background:var(--brand);color:#fff;padding:7px 14px;font-size:13px;white-space:nowrap}
.hero-title{left:100px;top:208px;font-size:36px;color:#1b1b1b}
.hero-script{left:100px;top:266px;font-family:"Kaushan Script",cursive;font-size:46px;color:var(--brand-deep)}
.hero-sub{left:100px;top:333px;font-family:"Lato",sans-serif;font-weight:700;font-size:16px;color:#1b1b1b}
.dots{left:100px;top:466px;display:flex;gap:6px}
.dots i{width:11px;height:11px;border-radius:50%;border:2px solid var(--band-dark)}
.dots i:first-child{background:var(--band-dark)}

/* intro */
.intro-title{left:100px;top:608px;font-size:26px;color:var(--brand-deep)}
.intro-rule{left:100px;top:644px;width:666px;height:1px;background:#d6dbde}
.intro-lead{left:100px;top:668px;font-weight:700;font-size:14px;color:#222}
.intro-copy{left:100px;top:700px;width:666px}
.optin{left:797px;top:627px;width:305px;height:355px;background:var(--brand);padding:34px 28px;color:#fff;text-align:center}
.optin h3{font-family:"Lato",sans-serif;font-weight:900;font-size:16px;line-height:20px}
.optin p{font-size:11.5px;line-height:16px;margin:10px 0 20px}
.field{height:30px;background:#fff;color:#777;font-size:11px;text-align:left;padding:8px 8px;margin-bottom:12px}
.optin .submit{border:1px solid #fff;height:40px;margin-top:12px;display:flex;align-items:center;justify-content:center;font-family:"Lato",sans-serif;font-weight:700;font-size:13px}
.badge{left:1058px;top:594px;width:96px;height:96px;border-radius:50%;background:var(--berry);color:#fff;font-family:"Lato",sans-serif;font-weight:700;font-size:13px;display:flex;align-items:center;justify-content:center;text-align:center;line-height:16px}

/* program band */
.band{left:0;width:1200px;background:var(--band)}
.band-kicker{width:1200px;text-align:center;color:#d7eef8;font-family:"Lato",sans-serif;font-size:18px}
.band-title{width:1200px;text-align:center;color:#fff;font-size:24px}
.card{top:1181px;width:310px;height:400px;background:#f2f3f4}
.card-photo{width:310px;height:208px}
.card-icon{position:absolute;left:137px;top:194px;width:36px;height:36px;border-radius:50%;background:var(--brand-deep);border:3px solid #fff}
.card h4{margin:44px 20px 10px;text-align:center;font-family:"Lato",sans-serif;font-weight:700;font-size:16px;line-height:22px;color:#222}
.card p{text-align:center;margin:0 26px;font-size:12px;line-height:17px;color:var(--muted)}

/* founder */
.founder-photo{left:78px;top:1662px;width:230px;height:430px;background:linear-gradient(180deg,#c79a82 0%,#8fd14f 30%,#7cc142 55%,#3c3f4a 100%);border-radius:110px 110px 0 0}
.founder-kicker{left:398px;top:1692px;font-family:"Lato",sans-serif;font-weight:700;font-size:19px;color:#222}
.founder-name{left:398px;top:1726px;font-size:26px;color:var(--brand-deep)}
.founder-copy{left:398px;top:1776px;width:704px}
.founder-copy a{color:var(--berry)}

/* results */
.result{width:230px;text-align:center}
.result-ring{width:230px;height:230px;border-radius:50%;border:5px solid #4fb6e0}
.result-ring.olive{background:var(--olive)}
.result-ring.blue{background:#3aa0cf}
.result-ring .snap{width:118px;height:150px;margin:40px auto 0;background:linear-gradient(180deg,#e6e0dc,#b49a8c)}
.result h5{margin-top:26px;font-family:"Lato",sans-serif;font-weight:700;font-size:22px;color:#fff}
.result .role{font-size:12px;color:#d7eef8;margin-top:6px}
.result .stat{font-size:12px;color:#d7eef8;margin-top:6px}

/* equipment */
.equip-ring{left:-70px;top:2740px;width:380px;height:380px;border-radius:50%;background:#1aa0c4}
.equip-pack{left:40px;top:2780px;width:280px;height:290px;background:linear-gradient(160deg,#e05a7a 0%,#f1d3de 40%,#3b7fb3 75%,#25476b 100%);transform:rotate(-8deg)}
.equip-kicker{left:398px;top:2736px;font-family:"Lato",sans-serif;font-weight:700;font-size:19px;color:#222}
.equip-title{left:398px;top:2776px;font-size:22px;color:var(--brand-deep)}
.equip-sub{font-family:"Lato",sans-serif;font-weight:700;font-size:17px;color:var(--brand-deep)}
.tick-row{display:flex;gap:12px;width:704px}
.tick-row svg{flex:none;margin-top:2px}

/* footer */
.footer{left:0;top:3202px;width:1200px;height:338px;background:var(--footer)}
.footer-brand{left:96px;top:3300px;text-align:center;color:#cfcfcf;font-family:"Lato",sans-serif;font-weight:700;font-size:20px}
.footer-brand .brand-dot{margin:0 auto 10px;background:#cfcfcf}
.footer-brand small{display:block;font-size:11px;letter-spacing:2px;font-weight:400}
.col-title{font-family:"Lato",sans-serif;font-weight:700;font-size:14px;color:#eee;letter-spacing:1px}
.col-rule{width:210px;height:1px;background:#3a3a3a;margin-top:12px}
.links{list-style:none;margin-top:16px;font-size:13px;color:#aaa;line-height:29px}
.contact-item{display:flex;gap:14px;margin-top:18px;font-size:11.5px;color:#aaa;line-height:15px}
.contact-item b{display:block;color:#ddd;font-size:12px}
.ci{flex:none;width:34px;height:34px;border-radius:50%;border:1px solid #555;display:flex;align-items:center;justify-content:center}
.in{height:38px;border:1px solid #555;font-size:11px;color:#999;padding:10px}
.send{background:var(--brand-deep);color:#fff;font-size:11px;width:120px;height:38px;display:flex;align-items:center;justify-content:center;margin-top:14px}
.legal{left:0;top:3540px;width:1200px;height:53px;background:var(--footer-low)}
.legal p{position:absolute;left:100px;top:18px;font-size:12px;color:#888}
.social{position:absolute;left:950px;top:10px;display:flex;gap:10px}
.social i{width:32px;height:32px;border-radius:50%;border:1px solid #777}

/* welcome pop-up */
.shade{left:0;top:0;width:1200px;height:3593px;background:var(--shade)}
.popup{left:423px;top:195px;width:282px;height:282px;border-radius:50%;background:var(--brand);border:4px solid #fff;color:#fff;text-align:center;padding-top:38px}
.popup .p1{font-family:"Lato",sans-serif;font-weight:700;font-size:20px}
.popup .p2{font-family:"Lato",sans-serif;font-weight:700;font-size:30px;line-height:34px}
.popup .p3{font-family:"Lato",sans-serif;font-weight:700;font-size:17px;margin-top:8px}
.popup .p4{font-size:11.5px;line-height:15px;margin:12px 48px 0}
.popup .p5{font-family:"Kaushan Script",cursive;color:var(--red);font-size:28px;margin-top:8px;background:#fff;display:inline-block;padding:0 6px}
.close{left:679px;top:190px;width:36px;height:36px;border-radius:50%;background:var(--red);border:3px solid #fff}
</style>
</head>
<body>

<!-- header + hero -->
<section class="abs hero">
  <div class="abs hero-photo" role="img" aria-label="Smiling mum kneeling on a mat with a dumbbell in a bright living room"></div>
  <div class="abs brand"><span class="brand-dot"></span><span>Tidewell Mamas<small>HOME FITNESS</small></span></div>
  <nav class="abs nav"><span>Home</span><span>About Us</span><span>Program</span><span>Blog</span><span>Shop</span><span>Contact Us</span><span class="join">JOIN WITH US</span></nav>
  <h1 class="abs heading hero-title">Lose your baby weight</h1>
  <div class="abs hero-script">Bounce Back into shape</div>
  <div class="abs hero-sub">12 week Home Workout Program For Mums</div>
  <div class="btn" style="left:100px;top:383px;width:190px;height:48px">Get Started Now!</div>
  <div class="abs dots"><i></i><i></i><i></i><i></i><i></i></div>
</section>

<!-- intro -->
<h2 class="abs heading intro-title">Tidewell Mamas</h2>
<div class="abs intro-rule"></div>
<p class="abs intro-lead">Check out some of the awesome results already achieved by mums on our program</p>
<div class="abs copy intro-copy">
  <p>After a life time of competitive sports and as a qualified personal trainer, I thought I knew exactly what it would take to get my body back after having babies. I put on a massive 30 kgs with my first pregnancy and found myself in a situation for the first time in my life where I had to lose a lot of weight. You can imagine how frustrated I was to find that it took me 8 months to get even close to my pre-baby body, training and eating the same way I always had. I particularly struggled with my baby belly, that just wouldn't go away.</p>
  <p style="margin-top:12px">This sparked a huge determination and curiosity within me and I spent the next 2 years studying and researching the body and the training techniques for mums post pregnancy.</p>
</div>
<div class="btn" style="left:100px;top:905px;width:146px;height:44px">Read More</div>
<div class="abs optin">
  <h3>GET YOUR FREE TOP 10<br>BABY BELLY BLASTING TIPS</h3>
  <p>See our secret tips to a flatter yummy mummy tummy that you can start implementing for free today!</p>
  <div class="field">Name</div>
  <div class="field">Email</div>
  <div class="submit">GET IT FREE NOW!</div>
</div>
<div class="abs badge">For Free<br>Today!</div>

<!-- program band -->
<section class="abs band" style="top:1018px;height:625px"></section>
<div class="abs band-kicker" style="top:1070px">Join all the other mums achieving amazing results and</div>
<h2 class="abs heading band-title" style="top:1104px">Bounce back into the body that you deserve!</h2>
<article class="abs card" style="left:100px">
  <div class="card-photo" role="img" aria-label="Mum cuddling her baby" style="background:linear-gradient(160deg,#8a6a58,#d9b9a2 60%,#6d5348)"></div>
  <span class="card-icon"></span>
  <h4>Our unique 3 stage, 12 week training program</h4>
  <p>Gradually build back your fitness and core strength and also lose baby weight with our training circuit and fitness program</p>
</article>
<article class="abs card" style="left:445px">
  <div class="card-photo" role="img" aria-label="Mum exercising on a mat at home" style="background:linear-gradient(160deg,#9c9aa8,#d8d2cc 55%,#5a5f7a)"></div>
  <span class="card-icon"></span>
  <h4>Our unique 3 stage, 12 week training program</h4>
  <p>Gradually build back your fitness and core strength and also lose baby weight with our training circuit and fitness program</p>
</article>
<article class="abs card" style="left:790px">
  <div class="card-photo" role="img" aria-label="Mum doing a workout in her lounge room" style="background:linear-gradient(160deg,#6b4a3c,#a88270 55%,#3e2c26)"></div>
  <span class="card-icon"></span>
  <h4>Our unique 3 stage, 12 week training program</h4>
  <p>Gradually build back your fitness and core strength and also lose baby weight with our training circuit and fitness program</p>
</article>

<!-- founder -->
<div class="abs founder-photo" role="img" aria-label="Founder standing in a green workout top"></div>
<div class="abs founder-kicker">About Tidewell Mamas Founder</div>
<h2 class="abs heading founder-name">Marla Quenby</h2>
<div class="abs copy founder-copy">
  <p>After a life time of competitive sports and as a qualified personal trainer, I thought I knew exactly what it would take to get my body back after having babies. I put on a massive 30 kgs with my first pregnancy and found myself in a situation for the first time in my life where I had to lose a lot of weight. You can imagine how frustrated I was to find that it took me 8 months to get even close to my pre-baby body, training and eating the same way I always had. I particularly struggled with my baby belly, that just wouldn't go away no matter how many crunches I crunched!</p>
  <p style="margin-top:12px">This is how I came to create the <a>12 Week Home Workout Program For Mums</a>. I put pen to paper and wrote down all the training routines I used to get my body back after my second baby. I then tested it out on other mums to make sure it worked for others too and all of the mums I tested on lost at least 18cms across their body doing the program.</p>
</div>
<div class="btn" style="left:398px;top:1995px;width:120px;height:42px">Read More</div>

<!-- results band -->
<section class="abs band" style="top:2091px;height:591px;background:var(--band-dark)"></section>
<div class="abs band-kicker" style="top:2144px">Join all the other mums achieving amazing results and</div>
<h2 class="abs heading band-title" style="top:2178px">Our mums before after photos</h2>
<svg class="abs" style="left:0;top:2300px" width="1200" height="140" aria-hidden="true"><path d="M0 90 C200 20 400 130 600 70 S1000 20 1200 80" fill="none" stroke="#5cb7de" stroke-width="2" stroke-dasharray="6 6"/></svg>
<div class="abs result" style="left:93px;top:2256px"><div class="result-ring olive"><div class="snap" role="img" aria-label="Before and after photo"></div></div><h5>Marla</h5><div class="role">Tidewell Mamas Founder</div><div class="stat">Lost 12 kgs and 20 cms in 12 weeks</div></div>
<div class="abs result" style="left:359px;top:2256px"><div class="result-ring blue"><div class="snap" role="img" aria-label="Before and after photo"></div></div><h5>Tessa</h5><div class="role">Olympic Games Gold Medalist</div><div class="stat">Lost 20 cms in 12 weeks</div></div>
<div class="abs result" style="left:625px;top:2256px"><div class="result-ring olive"><div class="snap" role="img" aria-label="Before and after photo"></div></div><h5>Jo</h5><div class="role">Tidewell Mama</div><div class="stat">Lost 18cms in 8 weeks</div></div>
<div class="abs result" style="left:891px;top:2256px"><div class="result-ring blue"><div class="snap" role="img" aria-label="Before and after photo"></div></div><h5>Bea</h5><div class="role">Tidewell Mama</div><div class="stat">Lost 31 cms and 10kgs in 8 weeks</div></div>

<!-- equipment -->
<div class="abs equip-ring"></div>
<div class="abs equip-pack" role="img" aria-label="Program equipment pack with DVD and workout cards"></div>
<div class="abs equip-kicker">What's included in the program?</div>
<h2 class="abs heading equip-title">12 week home workout program - equipment pack</h2>
<div class="abs" style="left:398px;top:2822px">
  <div class="equip-sub">Our unique 3 stage, 12 week training program</div>
  <div class="tick-row copy" style="margin-top:12px">
    <svg width="16" height="16" viewBox="0 0 16 16"><path d="M2 8l4 4 8-9" fill="none" stroke="#2b8fbd" stroke-width="3"/></svg>
    <p>Gradually build back your fitness and core strength and also lose baby weight with our training circuit and fitness program. We take you through 6 workout programs that increase with intensity and are designed for new mums as well as experienced mums.</p>
  </div>
  <div class="equip-sub" style="margin-top:18px">Full Instructional Workout DVD and program cards for each program</div>
  <div class="tick-row copy" style="margin-top:12px">
    <svg width="16" height="16" viewBox="0 0 16 16"><path d="M2 8l4 4 8-9" fill="none" stroke="#2b8fbd" stroke-width="3"/></svg>
    <p>You can either do your home workout along with us on DVD, or your program cards and do it yourself while hanging with your family watching your favourite tv shows.</p>
  </div>
</div>
<div class="btn" style="left:398px;top:3052px;width:120px;height:42px">Read More</div>

<!-- footer -->
<footer class="abs footer"></footer>
<div class="abs footer-brand"><div class="brand-dot"></div>Tidewell Mamas<small>HOME FITNESS</small></div>
<div class="abs" style="left:362px;top:3242px">
  <div class="col-title">QUICK LINKS</div><div class="col-rule" style="width:160px"></div>
  <ul class="links"><li>› Home</li><li>› About Us</li><li>› Programs</li><li>› Blog</li><li>› Shop</li><li>› Contact</li></ul>
</div>
<div class="abs" style="left:560px;top:3242px">
  <div class="col-title">CONTACT US</div><div class="col-rule"></div>
  <div class="contact-item"><span class="ci"><svg width="14" height="18" viewBox="0 0 14 18"><path d="M7 1a6 6 0 0 0-6 6c0 5 6 10 6 10s6-5 6-10a6 6 0 0 0-6-6z" fill="none" stroke="#aaa" stroke-width="1.5"/><circle cx="7" cy="7" r="2" fill="#aaa"/></svg></span><span><b>ADDRESS,</b>14 Harbourne Lane,<br>Kestrel Bay</span></div>
  <div class="contact-item"><span class="ci"><svg width="16" height="16" viewBox="0 0 16 16"><path d="M4 1l3 4-2 2a9 9 0 0 0 4 4l2-2 4 3-2 3C7 15 1 9 1 3z" fill="none" stroke="#aaa" stroke-width="1.4"/></svg></span><span><b>PHONE:</b>040 118 2297</span></div>
  <div class="contact-item"><span class="ci"><svg width="16" height="12" viewBox="0 0 16 12"><rect x="1" y="1" width="14" height="10" fill="none" stroke="#aaa" stroke-width="1.4"/><path d="M1 1l7 6 7-6" fill="none" stroke="#aaa" stroke-width="1.4"/></svg></span><span><b>Mail:</b>hello@tidewellmamas.com.au</span></div>
</div>
<div class="abs" style="left:832px;top:3242px;width:270px">
  <div class="col-title">CONTACT FORM</div><div class="col-rule" style="width:270px"></div>
  <div style="display:flex;gap:10px;margin-top:18px"><div class="in" style="flex:1">Name</div><div class="in" style="flex:1">Phone</div></div>
  <div class="in" style="height:68px;margin-top:10px">Message</div>
  <div class="send">SEND MESSAGE</div>
</div>
<div class="abs legal">
  <p>Copyright © 2018 Tidewell Mamas. All Right Reserved</p>
  <div class="social"><i></i><i></i><i></i><i></i></div>
</div>

<!-- welcome pop-up -->
<div class="abs shade"></div>
<div class="abs popup">
  <div class="p1">GET YOUR</div>
  <div class="p2">FREE TOP 10</div>
  <div class="p3">BABY BELLY BLASTING TIPS</div>
  <div class="p4">See our secret tips to a flatter yummy mummy tummy that you can start implementing</div>
  <div class="p5">for free today!</div>
</div>
<svg class="abs close" viewBox="0 0 36 36" aria-label="Close"><path d="M12 12l8 8M20 12l-8 8" stroke="#fff" stroke-width="3" transform="translate(2 2)"/></svg>

</body>
</html>
```